Veltrano.co - Polar Expeditions Specialists

We need a modern, visually striking business card for Veltrano.co, a company specialized in selling expedition cruises to the most remote regions on Earth, with a focus on the Arctic and Antarctica. The design should instantly communicate that the cardholder is an expert in polar travel. Use clean, premium aesthetics with cool tones like icy blue and white, possibly incorporating polar imagery (ice, glaciers, penguins, etc.)

Attached the logo

Contact Information for Business Card

Feels high-end and trustworthy.. Visually memorable — encourages people to keep it

Colors
0054AA
0677BA
7BADD7
CADEEF
E8F1F8

Requirements
Must have
• ice, glaciers, penguins, montains
Nice to have
• modern, transparente,

```html
<!DOCTYPE html>
<html lang="en">
<head>
<meta charset="utf-8">
<title>Veltrano.co Business Card</title>
<link rel="stylesheet" href="https://fonts.googleapis.com/css2?family=Poppins:wght@500;600;700&family=Montserrat:wght@400;500&display=swap">
<style>
  :root {
    --bg: #e4e3e5;
    --brand-blue: #3576b5;
    --ink-blue: #3567b0;
    --ink-dark: #1d1d22;
    --white: #ffffff;
    --mark-faint: #edf0f7;
  }
  * { margin: 0; padding: 0; box-sizing: border-box; }
  html, body { width: 1200px; height: 1108px; overflow: hidden; }
  body { background: var(--bg); position: relative; font-family: "Montserrat", sans-serif; }

  .card { position: absolute; overflow: hidden; }

  .card-front { left: 219px; top: 50px; width: 775px; height: 473px; background: var(--white); }
  .front-mark { position: absolute; left: 200px; top: 40px; width: 440px; height: 440px; border-radius: 50%; background: var(--mark-faint); }
  .front-brand { position: absolute; left: 108px; top: 204px; width: 272px; text-align: center; }
  .brand-name { font-family: "Poppins", sans-serif; font-weight: 700; color: var(--ink-blue); font-size: 51px; line-height: 1; letter-spacing: -0.5px; white-space: nowrap; }
  .card-front .brand-name { font-size: 45px; }
  .brand-tagline { font-family: "Poppins", sans-serif; font-weight: 600; color: var(--ink-blue); font-size: 16px; margin-top: 10px; white-space: nowrap; }

  .divider { position: absolute; left: 398px; top: 164px; width: 2px; height: 150px; background: var(--ink-blue); }
  .contact { position: absolute; left: 410px; top: 162px; }
  .person-name { font-family: "Poppins", sans-serif; font-weight: 600; color: var(--ink-blue); font-size: 29px; line-height: 1.1; }
  .person-title { font-size: 17px; color: var(--ink-dark); margin-top: 4px; margin-bottom: 12px; }
  .contact-row { display: flex; align-items: center; gap: 8px; font-size: 17px; color: var(--ink-dark); height: 30px; }
  .contact-row svg { width: 18px; height: 18px; fill: var(--brand-blue); flex: none; }

  .address-band { position: absolute; left: 0; top: 390px; width: 100%; height: 50px; background: var(--brand-blue); color: var(--white); font-size: 17px; display: flex; align-items: center; justify-content: center; }

  .card-back { left: 217px; top: 568px; width: 777px; height: 457px; background: var(--brand-blue); text-align: center; }
  .back-mark { position: absolute; left: 328px; top: 122px; width: 122px; height: 122px; border-radius: 50%; background: var(--white); }
  .back-brand { position: absolute; left: 0; right: 0; top: 280px; }
  .card-back .brand-name { color: var(--white); font-size: 63px; }
  .card-back .brand-tagline { color: var(--white); font-size: 21px; margin-top: 8px; }
</style>
</head>
<body>
  <section class="card card-front">
    <div class="front-mark" aria-hidden="true"></div>
    <div class="front-brand">
      <div class="brand-name">Veltrano.co</div>
      <div class="brand-tagline">Polar Expeditions Specialists</div>
    </div>
    <div class="divider"></div>
    <div class="contact">
      <div class="person-name">Marco Ellison</div>
      <div class="person-title">Managing Director</div>
      <div class="contact-row">
        <svg viewBox="0 0 24 24" aria-hidden="true"><path d="M6.6 10.8c1.4 2.8 3.8 5.1 6.6 6.6l2.2-2.2c.3-.3.7-.4 1-.2 1.1.4 2.3.6 3.6.6.6 0 1 .4 1 1V20c0 .6-.4 1-1 1C10.6 21 3 13.4 3 4c0-.6.4-1 1-1h3.5c.6 0 1 .4 1 1 0 1.3.2 2.5.6 3.6.1.3 0 .7-.2 1z"/></svg>
        <span>(555)014-2870</span>
      </div>
      <div class="contact-row">
        <svg viewBox="0 0 24 24" aria-hidden="true"><path d="M3 6h18v12H3z"/><path d="M3 7l9 6.5L21 7" fill="none" stroke="#fff" stroke-width="1.5"/></svg>
        <span>info@veltrano.co</span>
      </div>
      <div class="contact-row">
        <svg viewBox="0 0 24 24" aria-hidden="true"><circle cx="12" cy="12" r="9"/><path d="M3 12h18M12 3c3 3 3 15 0 18M12 3c-3 3-3 15 0 18" fill="none" stroke="#fff" stroke-width="1.3"/></svg>
        <span>www.veltrano.co</span>
      </div>
    </div>
    <div class="address-band">42 Harbor Point Drive Aldenbrook, NJ 07123 USA</div>
  </section>

  <section class="card card-back">
    <div class="back-mark" aria-hidden="true"></div>
    <div class="back-brand">
      <div class="brand-name">Veltrano.co</div>
      <div class="brand-tagline">Polar Expeditions Specialists</div>
    </div>
  </section>
</body>
</html>
```